Salon and Spa Distributor Business Card

Need a business card. We are are distributor in the salon and spa industry. We identify with natural beauty. Need a card with:
Company Name: Petal Quarry"
Title: "President & CEO"
Address
Company Phone number
email
website
Tag Line:" The Professional Salon Source"

Industry/Entity Type

Business

Contact Information for Business Card

Name: Dov Strommen
Title: "President & CEO"
Address: 31 Harlow Ln, Bexmoor, NJ 07813
Company Phone number: 800-463-5918
email: dovstrommen@petalquarry.example
website: www.petalquarry.example

Requirements
Should not have
• No black backgrounds

```html
<!DOCTYPE html>
<html lang="en">
<head>
<meta charset="utf-8">
<title>Petal Quarry – Business Card</title>
<link rel="stylesheet" href="https://fonts.googleapis.com/css2?family=Didact+Gothic&family=Arimo&display=swap">
<style>
  :root {
    --card-bg: #ffffff;
    --teal: #4cc4be;
    --leaf-light: #8cf05a;
    --leaf-mid: #5fd630;
    --leaf-deep: #2fa81c;
    --contact-grey: #858c92;
  }
  html, body {
    margin: 0;
    padding: 0;
    overflow: hidden;
    background: var(--card-bg);
  }
  .card {
    position: relative;
    width: 1200px;
    height: 720px;
    background: var(--card-bg);
    overflow: hidden;
    font-family: "Arimo", Arial, sans-serif;
  }
  .card-art {
    position: absolute;
    inset: 0;
    width: 1200px;
    height: 720px;
  }
  .company {
    position: absolute;
    right: 155px;
    top: 38px;
    margin: 0;
    color: var(--teal);
    font-family: "Didact Gothic", "Century Gothic", sans-serif;
    font-size: 26px;
    font-weight: 400;
    letter-spacing: 5px;
    line-height: 1;
  }
  .identity {
    position: absolute;
    right: 155px;
    top: 100px;
    text-align: right;
    color: var(--teal);
    font-family: "Didact Gothic", "Century Gothic", sans-serif;
  }
  .identity__name {
    margin: 0;
    font-size: 76px;
    font-weight: 400;
    line-height: 1;
    letter-spacing: 0.5px;
  }
  .identity__title {
    margin: 8px 0 0;
    font-size: 22px;
    letter-spacing: 4.5px;
  }
  .contact {
    position: absolute;
    left: 45px;
    top: 282px;
    margin: 0;
    padding: 0;
    list-style: none;
  }
  .contact__item {
    display: flex;
    align-items: center;
    height: 74px;
    margin-bottom: 36px;
  }
  .contact__icon {
    width: 74px;
    height: 74px;
    flex: none;
  }
  .contact__lines {
    margin-left: 20px;
    color: var(--contact-grey);
    font-size: 21px;
    line-height: 31px;
    white-space: nowrap;
  }
  .tagline {
    position: absolute;
    left: 879px;
    top: 543px;
    margin: 0;
    color: var(--teal);
    font-family: "Didact Gothic", "Century Gothic", sans-serif;
    font-size: 30px;
    font-weight: 400;
    line-height: 43px;
    letter-spacing: 4.6px;
  }
</style>
</head>
<body>
<main class="card">
  <svg class="card-art" viewBox="0 0 1200 720" xmlns="http://www.w3.org/2000/svg">
    <defs>
      <linearGradient id="swoosh-gradient" x1="0" y1="0" x2="1" y2="0">
        <stop offset="0" stop-color="var(--leaf-mid)"/>
        <stop offset="0.5" stop-color="var(--leaf-light)"/>
        <stop offset="1" stop-color="var(--leaf-mid)"/>
      </linearGradient>
      <radialGradient id="illustration-gradient" cx="0.55" cy="0.5" r="0.6">
        <stop offset="0" stop-color="var(--leaf-light)" stop-opacity="0.85"/>
        <stop offset="0.7" stop-color="var(--leaf-mid)" stop-opacity="0.5"/>
        <stop offset="1" stop-color="var(--leaf-deep)" stop-opacity="0"/>
      </radialGradient>
      <radialGradient id="sprig-gradient" cx="0.5" cy="0.5" r="0.5">
        <stop offset="0" stop-color="var(--leaf-mid)" stop-opacity="0.7"/>
        <stop offset="1" stop-color="var(--leaf-light)" stop-opacity="0"/>
      </radialGradient>
    </defs>

    <path class="swoosh"
          d="M0 118 C 90 88, 170 82, 250 92 C 420 112, 520 190, 660 232 C 800 276, 900 298, 990 290 C 1080 282, 1140 220, 1185 170
             L 1184 176 C 1140 232, 1080 292, 990 298 C 900 306, 800 286, 658 242 C 520 200, 420 122, 250 102 C 170 94, 90 100, 0 128 Z"
          fill="url(#swoosh-gradient)"/>

    <rect class="sprig" x="235" y="22" width="80" height="72" rx="36"
          fill="url(#sprig-gradient)" role="img" aria-label="Sprig of green leaves on the swoosh"/>
    <rect class="sprig" x="20" y="122" width="118" height="62" rx="31"
          fill="url(#sprig-gradient)" role="img" aria-label="Falling green leaves"/>

    <rect class="illustration" x="505" y="256" width="355" height="444" rx="160"
          fill="url(#illustration-gradient)" role="img"
          aria-label="Green illustration of a woman in profile with flowing leafy hair"/>
  </svg>

  <p class="company">Petal Quarry</p>

  <header class="identity">
    <h1 class="identity__name">Dov Strommen</h1>
    <p class="identity__title">President &amp; CEO</p>
  </header>

  <ul class="contact">
    <li class="contact__item">
      <svg class="contact__icon" viewBox="0 0 74 74" aria-hidden="true">
        <rect width="74" height="74" fill="var(--teal)"/>
        <path d="M26 18c2 0 4 5 5 8 .5 2-2 3.5-2.5 5 1.5 4.5 6 9.5 11 11.5 1.5-.5 3-3 5-2.5 3 1 8 3 8 5 0 3-3 7-7 7-11 0-25-14-25-27 0-4 3.5-7 5.5-7z" fill="#fff"/>
      </svg>
      <div class="contact__lines">800-463-5918<br>(+1) 800-463-5918</div>
    </li>
    <li class="contact__item">
      <svg class="contact__icon" viewBox="0 0 74 74" aria-hidden="true">
        <rect width="74" height="74" fill="var(--teal)"/>
        <path d="M37 12c-9 0-16 7-16 16 0 12 16 33 16 33s16-21 16-33c0-9-7-16-16-16zm0 23a7 7 0 1 1 0-14 7 7 0 0 1 0 14z" fill="#fff"/>
      </svg>
      <div class="contact__lines">Bexmoor, NJ 07813<br>31 Harlow Ln</div>
    </li>
    <li class="contact__item">
      <svg class="contact__icon" viewBox="0 0 74 74" aria-hidden="true">
        <rect width="74" height="74" fill="var(--teal)"/>
        <g fill="none" stroke="#fff" stroke-width="2.6">
          <circle cx="37" cy="37" r="19"/>
          <ellipse cx="37" cy="37" rx="8" ry="19"/>
          <line x1="37" y1="18" x2="37" y2="56"/>
          <line x1="18" y1="37" x2="56" y2="37"/>
          <line x1="21" y1="28" x2="53" y2="28"/>
          <line x1="21" y1="46" x2="53" y2="46"/>
        </g>
      </svg>
      <div class="contact__lines">www.petalquarry.example<br>dovstrommen@petalquarry.example</div>
    </li>
  </ul>

  <p class="tagline">The<br>Professional<br>Salon Source</p>
</main>
</body>
</html>
```